Backdrop Banner to be designed for a kids handwriting company

We are an occupational therapy company that helps children improve their handwriting. We give online lessons and make how-to videos for the kids to watch. We are looking for a backdrop to be designed that can be placed on a roller blind to use when needed. Size to be 183cm (width) x200cm (height). The final design needs to be produced in a format that can be uploaded to a printing company for them to produce.

We need our logo to be displayed. Our corporate colours are: #ff0069, #2abeb0, #ffc700, #93db40, #322e58. If you wish to see our current 'look' go to www.penpathlearning.co.uk. We can tell you our fonts if asked.

We work with children aged 6 to 16 years, mainly 10 to 13 years. In the past, I have placed motivational stickers on the back of my wall. Many of the children we see have lost confidence in themselves hence the words 'Believe in yourself', 'Make it happen' etc. were chosen. We teach them how to write clearly so the teachers can read/mark their work, parents are happy and we boost their self confidence. We are open to positive words or doodle style images but they cannot be cutesy. The backdrop must not overpower a lesson and take away the kid's focus.

I have included some ideas, our logo and a picture of what is the backdrop in my office.
1. We are open to keeping everything in the right-hand corner of the screen so the kids see us and any image is to the right (as per the picture). If doing this the images will need to sit from 30cm to 80cm from the top of the blind when fully down. Width needed is probably 65cm.
2. We are open to the parkour concept of words and images going across the whole backdrop or on the right hand side.
3. We are open to the backdrop having one image on its own whether that be random or specific images.
4. If using any writing the font has to be readable, no imitation of 'bad' handwriting. We see kids at any time of the day so we cannot have it say 'Good morning'.

We are hoping you will be inspired by this project as we'd love to work with you and see your ideas.

UPDATE 1 - 03.08.23: Based on the designs submitted so far please watch the wording of any motivational words and keep in mind this is a backdrop banner only the top half is likely to be seen on screen and there will be a person sitting in front of your design.

UPDATE 2 - 04.08.23: Mock up images with measurements added to help you design this backdrop for a video.

UPDATE: Based on the designs submitted so far please watch the wording of any motivational words and keep in mind this is a backdrop banner only the top half is likely to be seen on screen and there will be a person sitting in front of your design.

Supplied this in the brief

Other font styles liked:
• Business fonts on website are Kind Heart, Logo is Typo Round Regular

• Supplied this in the brief

```html
<!DOCTYPE html>
<html lang="en">
<head>
<meta charset="utf-8">
<title>Believe in yourself – Backdrop Banner</title>
<link rel="stylesheet" href="https://fonts.googleapis.com/css2?family=Patrick+Hand&family=Arimo:wght@400&display=swap">
<style>
  :root {
    --page: #ffffff;
    --measure: #e2a01f;
    --navy: #221c6b;
    --indigo: #2a2f7e;
    --ocean: #24668e;
    --teal: #2abeb0;
    --lime: #a8d43a;
    --amber: #ffc700;
    --pink: #ff0069;
    --plum: #7a2a6e;
    --blue: #2a5fb8;
    --white: #ffffff;
    --ink: #1e1616;
  }
  html, body {
    margin: 0;
    padding: 0;
    width: 1120px;
    height: 1200px;
    overflow: hidden;
    background: var(--page);
  }
  .canvas {
    position: relative;
    width: 1120px;
    height: 1200px;
  }
  .dimension {
    position: absolute;
    font-family: "Arimo", Arial, sans-serif;
    color: var(--measure);
    font-size: 25px;
    letter-spacing: -0.5px;
    line-height: 1;
  }
  .dimension--width { left: 532px; top: 62px; }
  .dimension--height {
    left: 60px; top: 627px;
    transform: translate(-50%, -50%) rotate(-90deg);
    white-space: nowrap;
  }
  .banner {
    position: absolute;
    left: 85px;
    top: 104px;
    width: 965px;
    height: 1057px;
    overflow: hidden;
    outline: 1px solid var(--measure);
    background: linear-gradient(180deg, var(--navy) 0%, var(--navy) 42%, var(--ocean) 72%, var(--teal) 100%);
  }
  .banner__burst {
    position: absolute;
    left: 0; top: 0;
    width: 965px; height: 1057px;
  }
  .banner__child {
    position: absolute;
    left: 539px;
    top: 310px;
    width: 186px;
    height: 252px;
    border-radius: 44% 44% 10% 10%;
    background: linear-gradient(180deg, #3a2418 0%, #6b4a34 30%, #e9e4de 55%, var(--ink) 100%);
  }
  .banner__headline {
    position: absolute;
    left: 491px;
    top: 197px;
    margin: 0;
    font-family: "Patrick Hand", "Comic Sans MS", cursive;
    font-weight: 400;
    font-size: 52px;
    line-height: 1;
    color: var(--white);
    text-shadow: 2px 3px 6px rgba(10, 10, 40, 0.6);
    white-space: nowrap;
  }
  .banner__brand {
    position: absolute;
    left: 676px;
    top: 518px;
    margin: 0;
    font-family: "Patrick Hand", "Comic Sans MS", cursive;
    font-weight: 400;
    font-size: 30px;
    line-height: 1;
    color: var(--white);
    white-space: nowrap;
  }
  .guides {
    position: absolute;
    left: 0; top: 0;
    width: 1120px; height: 1200px;
    pointer-events: none;
  }
  .guides line { stroke: var(--measure); stroke-width: 1; }
</style>
</head>
<body>
<div class="canvas">
  <div class="dimension dimension--width">183cm</div>
  <div class="dimension dimension--height">200 cm</div>

  <section class="banner">
    <svg class="banner__burst" viewBox="0 0 965 1057" role="img" aria-label="Rainbow starburst of overlapping coloured rays around a bright lime star">
      <defs>
        <radialGradient id="burstGlow" cx="551" cy="376" r="560" gradientUnits="userSpaceOnUse">
          <stop offset="0" stop-color="var(--lime)" stop-opacity="1"/>
          <stop offset="0.18" stop-color="var(--lime)" stop-opacity="0.9"/>
          <stop offset="0.32" stop-color="var(--amber)" stop-opacity="0.55"/>
          <stop offset="0.48" stop-color="var(--pink)" stop-opacity="0.4"/>
          <stop offset="0.68" stop-color="var(--blue)" stop-opacity="0.3"/>
          <stop offset="1" stop-color="var(--plum)" stop-opacity="0"/>
        </radialGradient>
      </defs>
      <ellipse cx="551" cy="376" rx="560" ry="600" fill="url(#burstGlow)"/>
    </svg>

    <div class="banner__child" role="img" aria-label="Illustration of a child in a striped top, seen from behind, writing letters in the air"></div>

    <h1 class="banner__headline">Believe in yourself</h1>
    <p class="banner__brand">PenPath Learning</p>
  </section>

  <svg class="guides" viewBox="0 0 1120 1200" aria-hidden="true">
    <line x1="945" y1="104" x2="945" y2="657"/>
    <line x1="576" y1="315" x2="1050" y2="315"/>
    <line x1="576" y1="657" x2="1050" y2="657"/>
    <line x1="576" y1="315" x2="576" y2="657"/>
  </svg>
</div>
</body>
</html>
```